Human Resource Consulting practice needs a business card design

We need a business card design (double sided colour) for our Human Resource (HR) consulting practice in regional New South Wales, australia. Our business name is Staff Compass. We support small and medium business across the Mid North Coast of New South Wales by providing them with outsourced HR support, services and products to help them achieve compliance with workplace legislation and across all areas of the employment lifecycle from recruitment to termination and everything in between. Our corporate colours are hot pink and black. The final design should communicate professionalism, trust, people focus.
I have attached the current (old) business card for your reference.

Target Market(s)

Business owners and high level managers

Industry/Entity Type

Business

Contact Information for Business Card

Name
Title
Phone no
Mobile no
Address
PO Box
email address
website

Colors
e34197

Requirements
Must have
• Tempate for changing business card personal details including Name, position title, mobile number, email address.
• Keep current logo and colours as per attached
• Logo must be presented in 2 colours or black only not white
Nice to have
• One side logo and graphic only other side logo and personal details
Should not have
• Should not be the same as the current version (attached) but a modern interpretation.
• Does not need a busy reverse side with our list of services as per current version. I feel this is too busy.
• No photos

```html
<!DOCTYPE html>
<html lang="en">
<head>
<meta charset="utf-8">
<title>Staff Compass – Business Card</title>
<link rel="stylesheet" href="https://fonts.googleapis.com/css2?family=Exo+2:wght@400;500;600&display=swap">
<style>
  :root {
    --pink: #e34197;
    --charcoal: #3a3a3c;
    --ink: #2b2b2b;
    --grey-text: #555558;
    --paper: #ffffff;
    --stage: #e9e9eb;
    --silver: #d4d4d6;
  }
  * { margin: 0; padding: 0; box-sizing: border-box; }
  html, body {
    width: 1200px; height: 771px; overflow: hidden;
    background: var(--stage);
    font-family: "Exo 2", sans-serif;
  }
  .sheet {
    width: 1200px; height: 771px;
    display: flex; align-items: center; justify-content: center; gap: 40px;
  }
  .card {
    position: relative;
    width: 540px; height: 309px;
    background: var(--paper);
    overflow: hidden;
    box-shadow: 0 2px 10px rgba(0,0,0,0.12);
  }
  /* Front: logo only */
  .card--front { display: flex; align-items: center; justify-content: center; }
  .wordmark {
    display: flex; align-items: center; gap: 10px;
    color: var(--pink); font-weight: 600; font-size: 44px; letter-spacing: 0.5px;
  }
  .wordmark__dot {
    width: 12px; height: 12px; background: var(--pink); border-radius: 50%;
  }
  /* Back: logo + details */
  .card--back .wordmark {
    position: absolute; left: 30px; top: 28px; font-size: 30px; gap: 7px;
  }
  .card--back .wordmark__dot { width: 8px; height: 8px; }
  .address {
    position: absolute; left: 32px; top: 80px;
    font-size: 11.5px; line-height: 1.45; color: var(--grey-text); letter-spacing: 0.4px;
  }
  .swoosh { position: absolute; left: 0; top: 0; width: 540px; height: 309px; }
  .person {
    position: absolute; right: 30px; top: 112px; text-align: right;
  }
  .person__name { color: var(--pink); font-size: 17px; font-weight: 500; letter-spacing: 0.6px; }
  .person__title { color: var(--ink); font-size: 11.5px; letter-spacing: 0.5px; margin-top: 2px; }
  .contacts {
    position: absolute; right: 30px; top: 178px;
    list-style: none; text-align: right;
  }
  .contacts li {
    display: flex; align-items: center; justify-content: flex-end; gap: 8px;
    font-size: 10.5px; color: var(--grey-text); letter-spacing: 0.4px; height: 17px;
  }
  .contacts svg { width: 11px; height: 11px; fill: var(--pink); flex: none; }
</style>
</head>
<body>
<main class="sheet">
  <section class="card card--front" aria-label="Card front">
    <div class="wordmark"><span class="wordmark__dot"></span>Staff Compass</div>
  </section>

  <section class="card card--back" aria-label="Card back">
    <svg class="swoosh" viewBox="0 0 540 309" aria-hidden="true">
      <path d="M0 118 C 90 150, 170 210, 300 250 C 390 278, 470 292, 540 300 L540 309 L0 309 Z" fill="var(--pink)"/>
      <path d="M0 132 C 95 165, 175 222, 300 258 C 390 283, 470 296, 540 303 L540 309 L0 309 Z" fill="var(--paper)"/>
      <path d="M0 142 C 100 180, 180 240, 300 272 C 360 288, 420 300, 470 309 L0 309 Z" fill="var(--charcoal)"/>
      <path d="M130 309 C 220 292, 300 290, 380 298 C 420 302, 450 306, 470 309 Z" fill="var(--silver)"/>
    </svg>

    <div class="wordmark"><span class="wordmark__dot"></span>Staff Compass</div>
    <p class="address">Suite 4, 27 Harbour Street<br>Port Kellin</p>

    <div class="person">
      <p class="person__name">Mara Linton</p>
      <p class="person__title">Managing Director</p>
    </div>

    <ul class="contacts">
      <li>026 555 0148
        <svg viewBox="0 0 24 24" aria-label="Phone"><path d="M6.6 10.8a15 15 0 0 0 6.6 6.6l2.2-2.2c.3-.3.7-.4 1-.2 1.1.4 2.3.6 3.6.6.6 0 1 .4 1 1V20c0 .6-.4 1-1 1A17 17 0 0 1 3 4c0-.6.4-1 1-1h3.5c.6 0 1 .4 1 1 0 1.3.2 2.5.6 3.6.1.3 0 .7-.2 1z"/></svg>
      </li>
      <li>026 555 0149
        <svg viewBox="0 0 24 24" aria-label="Mobile"><path d="M7 1h10a2 2 0 0 1 2 2v18a2 2 0 0 1-2 2H7a2 2 0 0 1-2-2V3a2 2 0 0 1 2-2zm0 3v14h10V4z"/></svg>
      </li>
      <li>026 555 0150
        <svg viewBox="0 0 24 24" aria-label="Fax"><path d="M6 2h10l2 2v5H6zm-3 8h18a1 1 0 0 1 1 1v9a1 1 0 0 1-1 1H3a1 1 0 0 1-1-1v-9a1 1 0 0 1 1-1zm3 5v4h12v-4z"/></svg>
      </li>
      <li>hello@staffcompass.au
        <svg viewBox="0 0 24 24" aria-label="Email"><path d="M2 5h20v14H2zm2 2v.5l8 5 8-5V7z"/></svg>
      </li>
      <li>www.staffcompass.au
        <svg viewBox="0 0 24 24" aria-label="Website"><circle cx="12" cy="12" r="10"/></svg>
      </li>
    </ul>
  </section>
</main>
</body>
</html>
```